Website Home Page for Women's Health Medical Office

Redesign existing homepage for website using existing logo. Current website location is www.meadowcrestwomens.com. Please give it a modern, streamlined, playful feel.

Please give it a feminine feel and make it bright and cheerful using logo colors.

Target Market(s)

Women between the ages of 25-45

Industry/Entity Type

Medical Office

Coding

Coded - Design and coding required

Number of Pages Required

1 page

Font styles to use
Sans Serif
Other font styles liked:
• SEGOI UI script for text and GIL SANS for bold (or their equivilent)

Colors
E54698
E96AAD
F1A4CE
F9D9EA
FCEFF6

Requirements
Must have
• Existing logo. Logo Colors. Feminine, cheerful, simple design. all relevant contact information
Nice to have
• clean lines and streamlined look
Should not have
• Cluttered

```html
<!DOCTYPE html>
<html lang="en">
<head>
<meta charset="utf-8">
<title>Meadowcrest Women's – Brookhaven, CA</title>
<link rel="stylesheet" href="https://fonts.googleapis.com/css2?family=Montserrat:wght@500;600;700;800&family=Raleway:wght@400;500;600&display=swap">
<style>
:root{
  --pink:#E5007E;
  --pink-2:#E54698;
  --pink-3:#E96AAD;
  --pink-4:#F1A4CE;
  --pink-5:#F9D9EA;
  --pink-6:#FCEFF6;
  --ink:#1b1b1f;
  --text:#3b3b40;
  --muted:#f6f5f7;
  --white:#ffffff;
  --rule:#d9d9dd;
}
*{margin:0;padding:0;box-sizing:border-box}
html,body{width:1200px;height:3244px;overflow:hidden;background:var(--white)}
body{font-family:"Raleway",sans-serif;color:var(--text);position:relative}
a{text-decoration:none}
.abs{position:absolute}
.heading{font-family:"Montserrat",sans-serif;font-weight:800;color:var(--ink);text-transform:uppercase}
.rule{position:absolute;height:3px;width:50px;background:var(--pink)}
.btn{position:absolute;display:flex;align-items:center;justify-content:center;background:var(--pink);color:var(--white);font-family:"Montserrat",sans-serif;font-weight:800;text-transform:uppercase;border-radius:3px}
.copy{font-size:13.5px;line-height:17.6px;text-align:justify}
.copy p+p{margin-top:17px}

/* header */
.site-header{position:absolute;left:0;top:0;width:1200px;height:125px}
.brand{left:131px;top:44px;font-family:"Montserrat",sans-serif;font-weight:700;font-size:17px;color:var(--ink);display:flex;align-items:center;gap:9px}
.brand-dot{width:22px;height:22px;border-radius:50%;background:var(--pink-3);flex:none}
.contact{display:flex;align-items:center;gap:14px;font-family:"Montserrat",sans-serif;font-size:12.5px;color:var(--ink);font-weight:500;line-height:19px}
.contact strong{font-weight:600}
.contact-icon{width:27px;height:27px;border-radius:5px;background:var(--pink);display:flex;align-items:center;justify-content:center}
.nav{right:131px;top:86px;display:flex;font-family:"Montserrat",sans-serif;font-size:13px;font-weight:500;color:var(--ink)}
.nav a{color:inherit}
.nav a.active{color:var(--pink-2);text-decoration:underline;text-underline-offset:5px}

/* hero */
.hero{position:absolute;left:0;top:125px;width:1200px;height:522px;background:linear-gradient(90deg,#fbd7e7 0%,#fbd7e7 42%,#e8e1dc 62%,#d8cfc6 100%)}
.hero-photo{position:absolute;left:505px;top:0;width:695px;height:522px;background:radial-gradient(ellipse at 40% 45%,#e4d2c4 0%,#cbbcae 45%,#b9aea8 100%);-webkit-mask-image:linear-gradient(90deg,transparent 0,#000 18%);mask-image:linear-gradient(90deg,transparent 0,#000 18%)}
.hero-kicker{left:131px;top:110px;font-family:"Montserrat",sans-serif;font-size:24px;font-weight:500;color:var(--ink);border-bottom:2px solid var(--ink);padding-bottom:1px}
.hero-title{left:131px;top:168px;font-size:37px;line-height:48px}
.hero .btn{left:131px;top:288px;width:126px;height:48px;font-size:13px}
.hero-arrows{left:131px;top:407px;display:flex;gap:20px}

/* intro */
.intro-blob-bg{left:150px;top:708px;width:405px;height:420px;background:var(--pink-6);border-radius:58% 42% 40% 60%/40% 38% 62% 60%}
.intro-photo{left:200px;top:690px;width:340px;height:437px;background:linear-gradient(180deg,#6a4b3a 0%,#c59a86 28%,#2b3569 55%,#1f2a5a 100%);border-radius:50% 50% 48% 52%/38% 38% 62% 62%}
.intro-title{left:622px;top:745px;font-size:19px;line-height:29px}

/* services */
.services{position:absolute;left:0;top:1177px;width:1200px;height:790px;background:var(--muted)}
.services-title{left:0;width:1200px;top:50px;text-align:center;font-size:19px}
.services-sub{left:0;width:1200px;top:87px;text-align:center;font-size:17px;color:var(--ink)}
.service-img{position:absolute;width:208px;height:216px;border-radius:55% 45% 50% 50%/38% 62% 38% 62%}
.service-name{font-family:"Montserrat",sans-serif;font-weight:700;font-size:13px;color:var(--ink);text-transform:uppercase}
.service-text{font-size:11.7px;line-height:17.6px;margin-top:15px;width:225px}
.service .btn{position:static;margin-top:19px;width:93px;height:35px;font-size:9.5px}

/* specialists */
.spec-title{left:131px;top:2055px;font-size:19px}
.spec-photo{left:620px;top:2016px;width:450px;height:474px;background:linear-gradient(160deg,#f3efec 0%,#e9dcd4 40%,#d9b9a5 65%,#f4f1ef 100%)}

/* cta */
.cta{position:absolute;left:0;top:2546px;width:1200px;height:267px;background:linear-gradient(110deg,#ec2f93 0%,#e5007e 50%,#ea2c90 100%);color:var(--white);text-align:center}
.cta-kicker{position:absolute;left:0;width:1200px;top:44px;font-size:21px}
.cta-title{position:absolute;left:0;width:1200px;top:84px;font-family:"Montserrat",sans-serif;font-weight:800;font-size:28px}
.cta-btn{position:absolute;top:161px;height:50px;background:var(--white);color:var(--pink);font-family:"Montserrat",sans-serif;font-weight:800;font-size:14px;display:flex;align-items:center;justify-content:center}
.cta-or{position:absolute;left:590px;top:177px;font-family:"Montserrat",sans-serif;font-weight:700;font-size:11px}

/* footer */
.site-footer{position:absolute;left:0;top:2813px;width:1200px;height:431px;background:var(--muted)}
.footer-brand{left:131px;top:96px;font-family:"Montserrat",sans-serif;font-weight:700;font-size:18px;color:var(--ink);display:flex;align-items:center;gap:9px;white-space:nowrap}
.plans{list-style:none;font-size:12.5px;line-height:24px;color:var(--ink);top:40px}
.footer-rule{left:131px;width:938px;height:1px;background:var(--rule)}
.footer-nav{left:0;width:1200px;top:283px;display:flex;justify-content:center;gap:21px;font-family:"Montserrat",sans-serif;font-size:12px;color:var(--ink)}
.footer-line{left:0;width:1200px;text-align:center;font-family:"Montserrat",sans-serif;font-size:12px;color:var(--ink)}
</style>
</head>
<body>

<header class="site-header">
  <div class="abs brand"><span class="brand-dot"></span>Meadowcrest Women's</div>

  <div class="abs contact" style="left:531px;top:25px">
    <span class="contact-icon"><svg width="13" height="13" viewBox="0 0 24 24"><path fill="#fff" d="M6.6 10.8a15.1 15.1 0 0 0 6.6 6.6l2.2-2.2c.3-.3.7-.4 1-.2 1.1.4 2.3.6 3.6.6.6 0 1 .4 1 1V20c0 .6-.4 1-1 1A17 17 0 0 1 3 4c0-.6.4-1 1-1h3.5c.6 0 1 .4 1 1 0 1.3.2 2.5.6 3.6.1.3 0 .7-.2 1z"/></svg></span>
    <div>Call us<br><strong>(555) 014-2280</strong></div>
  </div>
  <div class="abs contact" style="left:699px;top:25px">
    <span class="contact-icon"><svg width="13" height="13" viewBox="0 0 24 24"><path fill="#fff" d="M6.6 10.8a15.1 15.1 0 0 0 6.6 6.6l2.2-2.2c.3-.3.7-.4 1-.2 1.1.4 2.3.6 3.6.6.6 0 1 .4 1 1V20c0 .6-.4 1-1 1A17 17 0 0 1 3 4c0-.6.4-1 1-1h3.5c.6 0 1 .4 1 1 0 1.3.2 2.5.6 3.6.1.3 0 .7-.2 1z"/></svg></span>
    <div>Call us<br><strong>555-014-2291</strong></div>
  </div>
  <div class="abs contact" style="left:855px;top:25px">
    <span class="contact-icon"><svg width="13" height="13" viewBox="0 0 24 24"><path fill="#fff" d="M3 5h18v14H3z"/><path fill="none" stroke="#E5007E" stroke-width="1.8" d="M3 6l9 7 9-7"/></svg></span>
    <div>Email us<br><strong>hello@meadowcrestwomens.com</strong></div>
  </div>

  <nav class="abs nav">
    <a class="active" href="#" style="margin-right:38px">HOME</a>
    <a href="#" style="margin-right:52px">SERVICES</a>
    <a href="#" style="margin-right:55px">RESOURCES</a>
    <a href="#" style="margin-right:55px">ABOUT US</a>
    <a href="#">CONTACT US</a>
  </nav>
</header>

<section class="hero">
  <div class="hero-photo" role="img" aria-label="Doctor with a tablet talking with a pregnant patient on a sofa"></div>
  <div class="abs hero-kicker">WELCOME TO</div>
  <h1 class="abs heading hero-title">Meadowcrest Women's,<br>Brookhaven, CA</h1>
  <a class="btn" href="#">Read more</a>
  <div class="abs hero-arrows">
    <svg width="18" height="26" viewBox="0 0 18 26"><path d="M14 2L4 13l10 11" fill="none" stroke="#555" stroke-width="3"/></svg>
    <svg width="18" height="26" viewBox="0 0 18 26"><path d="M4 2l10 11L4 24" fill="none" stroke="#555" stroke-width="3"/></svg>
  </div>
</section>

<section class="intro">
  <div class="abs intro-blob-bg"></div>
  <div class="abs intro-photo" role="img" aria-label="Smiling physician in navy scrubs with arms crossed"></div>
  <h2 class="abs heading intro-title">Serving Willow Springs<br>Medical Center</h2>
  <div class="rule" style="left:622px;top:826px"></div>
  <div class="abs copy" style="left:622px;top:866px;width:428px">
    <p>At Meadowcrest Women's in Brookhaven, California, we believe better health starts when the patient is educated. For this reason, we take time to listen to our patients concerns, explain each option available, and to answer any questions our patients may have so that they can make informed decisions. At Meadowcrest Women's, our providers tailor every procedure performed and treatment option recommended to meet the specific needs of our patients. We remain up-to-date on the latest technology and practice guidelines for women's health.</p>
    <p>Our medical providers will take time to give you the personalized health care you deserve. This includes taking time to listen to you and screening you for problems to help ensure that any health issues are diagnosed and treated as early as possible.</p>
  </div>
</section>

<section class="services">
  <h2 class="abs heading services-title">How can we help you?</h2>
  <div class="abs services-sub">Health Services Offered</div>
  <div class="rule" style="left:575px;top:131px"></div>

  <div class="service-img" role="img" aria-label="Pregnant woman holding her belly" style="left:128px;top:208px;background:linear-gradient(140deg,#e9e7e6,#cfc7c2 55%,#a79a93)"></div>
  <div class="abs service" style="left:361px;top:205px">
    <div class="service-name">Pregnancy care</div>
    <div class="service-text">Receiving regular care in pregnancy is important for the health of both you and your baby. Our obstetricians work with you every step of the way during your pregnancy and delivery to make sure your individual needs are met and co ensure this special journey is a memorable one.</div>
    <a class="btn" href="#">Read more</a>
  </div>

  <div class="service-img" role="img" aria-label="Hands holding a pack of birth control pills" style="left:616px;top:208px;background:linear-gradient(150deg,#f0c9ae,#e3a784 55%,#3c3535)"></div>
  <div class="abs service" style="left:849px;top:205px">
    <div class="service-name">Birth control</div>
    <div class="service-text">Our gynecologists are knowledgeable on all forms of birth control including the IUD, the implant, vaginal ringinsertion, birth control pills, and more! We would love to work with you to determine the best option for you and your lifestyle.</div>
    <a class="btn" href="#">Read more</a>
  </div>

  <div class="abs service" style="left:132px;top:507px">
    <div class="service-name">Well woman exams</div>
    <div class="service-text" style="width:220px">Our providers will help you to stay healthy by performing a physical exam on you annually. We will screen you for multiple health conditions that may pose a risk to you. This includes screening you for cancerous conditions of the breast, ovaries and cervix.</div>
    <a class="btn" href="#">Read more</a>
  </div>
  <div class="service-img" role="img" aria-label="Joyful woman celebrating at a table" style="left:369px;top:508px;background:linear-gradient(150deg,#f2f2f0,#d9d3cf 50%,#8f6d61)"></div>

  <div class="abs service" style="left:624px;top:507px">
    <div class="service-name">Women's health</div>
    <div class="service-text" style="width:215px">Whether you are dealing with painful or irregular periods, fibroids, or other women's health i ssues, we can help. We offer a variety of the most up-to-date treatment options to help you regain your lifestyle.</div>
    <a class="btn" href="#" style="margin-top:33px">Read more</a>
  </div>
  <div class="service-img" role="img" aria-label="Woman raising her arms in a sunlit meadow" style="left:862px;top:508px;background:linear-gradient(180deg,#f3dcc0,#e8b98c 45%,#a98a6b)"></div>
</section>

<section class="specialists">
  <h2 class="abs heading spec-title">Your OB/GYN specialists</h2>
  <div class="rule" style="left:131px;top:2099px"></div>
  <div class="abs copy" style="left:131px;top:2140px;width:424px">
    <p>Meadowcrest Women's offers you the best care possible in a personalized setting. We are currently accepting patients. Call our office now to make an appointment.</p>
    <p>Meadowcrest Women's (located near Willow Springs Hospital in Brookhaven, CA) is a medical office that specializes in Christ-centered healthcare for women of all ages. Our team of exclusively female providers have years of experience taking care of women with a variety of pregnancy and gynecology concerns.</p>
    <p>Whether you need a routine examination, help during your pregnancy, have questions on birth control, or another female concern, we offer the best care possible for our patients. That is why better health starts here.</p>
    <p>Our office provides you with an environment where you can feel comfortable and where you know you will be in good hands. Our providers are leaders women's health. Dr. Harlow is a board certified obstetrician and gynecologist. Dr. Amari is a board eligible obstetrician and gynecologist.</p>
  </div>
  <div class="abs spec-photo" role="img" aria-label="Mother holding her sleeping newborn"></div>
</section>

<section class="cta">
  <div class="cta-kicker">Better Health Starts Here!</div>
  <h2 class="cta-title">NOW ACCEPTING NEW PATIENTS</h2>
  <a class="cta-btn" href="#" style="left:223px;width:331px">CLICK HERE FOR AN APPOINTMENT</a>
  <span class="cta-or">OR</span>
  <a class="cta-btn" href="#" style="left:643px;width:274px">CALL US AT (555) 014-2280</a>
</section>

<footer class="site-footer">
  <div class="abs footer-brand"><span class="brand-dot" style="width:24px;height:24px"></span>Meadowcrest Women's</div>

  <ul class="abs plans" style="left:398px">
    <li>Alder Health</li><li>Inland Care Direct</li><li>Primewell of Oakridge</li><li>Primewell of Hillcrest</li><li>SilverPath</li><li>Harbor Medical Group</li><li>Vantage Service Plan</li>
  </ul>
  <ul class="abs plans" style="left:637px">
    <li>Valleyline Physicians</li><li>Northstar Open Access</li><li>Crestline Select</li><li>Bluewater Shield</li><li>Summit Health</li><li>Summit Local Plus</li><li>Veterans Family Plan</li>
  </ul>
  <ul class="abs plans" style="left:879px">
    <li>Evergreen Benefits</li><li>Federal Staff Plan</li><li>HealthBridge</li><li>Meridian Care</li><li>Steelcraft Trust Fund</li><li>Builders Health &amp; Welfare Fund</li><li>Postal Carriers Plan</li><li>Operators Benefit Fund</li>
  </ul>

  <div class="abs footer-rule" style="top:263px"></div>
  <nav class="abs footer-nav">
    <span>HOME</span><span>ABOUT US</span><span>NEWS</span><span>PATIENT RESOURCES</span><span>PRIVACY POLICY</span><span>CONTACT US</span>
  </nav>
  <div class="abs footer-rule" style="top:323px"></div>
  <div class="abs footer-line" style="top:354px">4180 Willow Bend Avenue, Suite 210, Brookhaven, CA 90210 &nbsp;&nbsp;|&nbsp;&nbsp; (555) 014-2280 &nbsp;&nbsp;|&nbsp;&nbsp; hello@meadowcrestwomens.com</div>
  <div class="abs footer-line" style="top:384px">Copyright © 2022 All Rights Reserved</div>
</footer>

</body>
</html>
```